RWT Fittings Ltd Business Cards

We need a business card with our business logo. We provide window and door installations on high-rises in west coast British Colombia, Canada.

I would like my business information and details on one side of the card, and the other side the company name with logo

Target Market(s)

General Contractors

Industry/Entity Type

Construction

Contact Information for Business Card

one side i want my company name and logo in the dark theme logo that i provided

Requirements
Must have
• Marco Peltieri, 16045518293, RWTFittings@mailbox-demo.com, 1407-5194 Linden Row Burnaby BC, V5H 2K9, Owner & Manager

```html
<!DOCTYPE html>
<html lang="en">
<head>
<meta charset="utf-8">
<title>RWT Fittings Ltd – Business Card</title>
<link rel="stylesheet" href="https://fonts.googleapis.com/css2?family=Ubuntu:wght@400;500;700&display=swap">
<style>
  :root {
    --stage: #232323;
    --card: #1e1f22;
    --card-deep: #17181a;
    --panel: #26282c;
    --blue: #27a7e1;
    --grey: #9c9d9f;
    --white: #f2f2f2;
    --emboss: #3b3c40;
  }
  * { margin: 0; padding: 0; box-sizing: border-box; }
  html, body { width: 1200px; height: 780px; overflow: hidden; background: var(--stage); }
  body { font-family: "Ubuntu", sans-serif; position: relative; }

  .card {
    position: absolute;
    top: 236px;
    width: 540px;
    height: 309px;
    background: var(--card);
    border-radius: 3px;
    overflow: hidden;
    box-shadow: 0 18px 40px rgba(0,0,0,.45);
  }
  .card--front { left: 40px; }
  .card--back { left: 620px; background: var(--card-deep); }

  /* front */
  .brand-mark {
    position: absolute;
    left: 30px; top: 28px;
    display: flex; align-items: center; gap: 10px;
    font-size: 26px; font-weight: 700;
    color: var(--emboss);
  }
  .brand-mark__square { width: 22px; height: 22px; background: var(--emboss); }

  .brand-watermark {
    position: absolute;
    right: 40px; bottom: 0;
    width: 250px; height: 200px;
    background: linear-gradient(135deg, var(--panel), rgba(38,40,44,.2));
  }

  .contact {
    position: absolute;
    right: 44px; bottom: 26px;
    text-align: right;
    color: var(--white);
  }
  .contact__name { font-size: 27px; font-weight: 700; line-height: 1; }
  .contact__first { color: var(--blue); }
  .contact__last { color: var(--grey); }
  .contact__role { font-size: 13px; font-weight: 500; margin-top: 5px; }
  .contact__address { font-size: 12.5px; line-height: 1.35; margin-top: 12px; }
  .contact__line {
    display: flex; align-items: center; justify-content: flex-end; gap: 8px;
    font-size: 12.5px; margin-top: 6px;
  }
  .contact__line:first-of-type { margin-top: 12px; }
  .contact__icon { width: 14px; height: 14px; fill: var(--blue); flex: none; }

  .accent-bar {
    position: absolute;
    right: 0; bottom: 40px;
    width: 16px; height: 66px;
    background: var(--blue);
  }

  /* back */
  .back-pattern {
    position: absolute; inset: 0;
    background: linear-gradient(120deg, #141517 0%, #1c1d20 55%, #5a5b5e 100%);
  }
  .back-brand {
    position: absolute;
    left: 300px; top: 196px;
    display: flex; align-items: center; gap: 7px;
    font-size: 15px; font-weight: 700;
    color: var(--blue);
  }
  .back-brand__square { width: 12px; height: 12px; background: var(--blue); }
</style>
</head>
<body>

  <section class="card card--front" aria-label="Card front">
    <div class="brand-mark">
      <span class="brand-mark__square"></span>
      <span>RWT Fittings Ltd</span>
    </div>

    <div class="brand-watermark" role="img" aria-label="Faint large company symbol in the background"></div>

    <div class="contact">
      <p class="contact__name"><span class="contact__first">Marco</span> <span class="contact__last">Peltieri</span></p>
      <p class="contact__role">Owner &amp; Manager</p>
      <p class="contact__address">1407-5194 Linden Row<br>Burnaby BC, V5H 2K9</p>
      <p class="contact__line">
        <span>1604 551 8293</span>
        <svg class="contact__icon" viewBox="0 0 24 24" aria-hidden="true"><path d="M6.6 10.8a15.1 15.1 0 0 0 6.6 6.6l2.2-2.2c.3-.3.7-.4 1-.2 1.1.4 2.3.6 3.6.6.6 0 1 .4 1 1V20c0 .6-.4 1-1 1A17 17 0 0 1 3 4c0-.6.4-1 1-1h3.5c.6 0 1 .4 1 1 0 1.3.2 2.5.6 3.6.1.3 0 .7-.2 1z"/></svg>
      </p>
      <p class="contact__line">
        <span>RWTFittings@mailbox-demo.com</span>
        <svg class="contact__icon" viewBox="0 0 24 24" aria-hidden="true"><path d="M2 6a2 2 0 0 1 2-2h16a2 2 0 0 1 2 2v12a2 2 0 0 1-2 2H4a2 2 0 0 1-2-2zm2 .5V7l8 5 8-5v-.5z"/></svg>
      </p>
    </div>

    <div class="accent-bar"></div>
  </section>

  <section class="card card--back" aria-label="Card back">
    <div class="back-pattern" role="img" aria-label="Repeating pattern of the company symbol fading from dark to silver"></div>
    <div class="back-brand">
      <span class="back-brand__square"></span>
      <span>RWT Fittings Ltd</span>
    </div>
  </section>

</body>
</html>
```